Irrigation Business needs their business cards modernised and revamped

I would like to keep my current logo, colours and revamp the format of the card.

I would like the card to be clean yet important.

Im not sure if you include texture but i would like the named logo to be indented into the card etc.

show me something alive and free something thats clinical to the point yet has a feel of achievement. i would like people to go nice card.

Target Market(s)

high end clients, corporate, sports field manger, the guys that make the decisions

Industry/Entity Type

Business

Contact Information for Business Card

nformation to be included

Dean Harlow (Director)
0487305526
dean@kolvat.biz
www.kestonfieldworks.com

instagram logo
google logo
facebook logo

Colors

Designer to choose colors to be used in the design.

Requirements
Nice to have
• indentations a really nice feel to the card good texture

```html
<!DOCTYPE html>
<html lang="en">
<head>
<meta charset="utf-8">
<title>Keston Fieldworks – Business Card</title>
<link rel="stylesheet" href="https://fonts.googleapis.com/css2?family=Open+Sans:wght@400;600;700;800&family=Open+Sans+Condensed:wght@700&display=swap">
<style>
  :root {
    --backdrop: #e9e6e2;
    --sky: #2ea6d8;
    --deep-blue: #2f6bb1;
    --paper: #f2f2f2;
    --white: #ffffff;
    --shadow: rgba(0, 0, 0, 0.18);
  }
  html, body {
    margin: 0;
    padding: 0;
    width: 1200px;
    height: 900px;
    overflow: hidden;
    background: var(--backdrop);
    font-family: "Open Sans", Arial, sans-serif;
  }
  .canvas {
    position: relative;
    width: 1200px;
    height: 900px;
  }
  .card {
    position: absolute;
    box-shadow: 0 6px 18px var(--shadow);
    overflow: hidden;
  }

  /* Front: contact side */
  .card-front {
    left: 78px;
    top: 34px;
    width: 588px;
    height: 365px;
    background: var(--sky);
  }
  .front-mark {
    position: absolute;
    left: 0;
    top: 0;
    width: 365px;
    height: 365px;
    background: var(--deep-blue);
  }
  .front-mark .disc {
    position: absolute;
    left: 8px;
    top: 8px;
    width: 349px;
    height: 349px;
    border-radius: 50%;
    background: var(--white);
    display: flex;
    align-items: center;
    justify-content: center;
  }
  .front-mark .mark-name {
    font-weight: 800;
    font-size: 30px;
    line-height: 1.15;
    color: var(--deep-blue);
    text-align: center;
    letter-spacing: 0.5px;
  }
  .person {
    position: absolute;
    right: 24px;
    top: 46px;
    text-align: right;
    color: var(--white);
  }
  .person .name {
    font-family: "Open Sans Condensed", "Open Sans", sans-serif;
    font-weight: 700;
    font-size: 22px;
    letter-spacing: 0.3px;
    line-height: 1;
  }
  .person .role {
    font-size: 14px;
    margin-top: 3px;
  }
  .social {
    position: absolute;
    right: 25px;
    top: 242px;
    display: flex;
    gap: 5px;
  }
  .social .dot {
    width: 22px;
    height: 22px;
    border-radius: 50%;
    background: rgba(255, 255, 255, 0.8);
  }
  .contact {
    position: absolute;
    right: 25px;
    top: 278px;
    color: var(--white);
    font-size: 15px;
    text-align: right;
  }
  .contact .line {
    display: flex;
    align-items: center;
    justify-content: flex-end;
    gap: 5px;
    height: 23px;
  }
  .contact svg { width: 16px; height: 16px; }

  /* Back: brand side */
  .card-back {
    left: 388px;
    top: 505px;
    width: 567px;
    height: 352px;
    background: var(--paper);
  }
  .brand-circle {
    position: absolute;
    left: 222px;
    top: 76px;
    width: 124px;
    height: 124px;
    border-radius: 50%;
    background: var(--sky);
    box-shadow: inset 0 0 0 4px var(--deep-blue), inset 0 0 0 7px var(--paper);
  }
  .brand-name {
    position: absolute;
    left: 0;
    right: 0;
    top: 208px;
    text-align: center;
    font-weight: 800;
    font-size: 37px;
    letter-spacing: -0.5px;
    color: var(--deep-blue);
  }
  .website {
    position: absolute;
    left: 0;
    right: 0;
    top: 296px;
    text-align: center;
    font-weight: 600;
    font-size: 15px;
    color: var(--deep-blue);
  }
</style>
</head>
<body>
<div class="canvas">

  <section class="card card-front">
    <div class="front-mark">
      <div class="disc">
        <span class="mark-name">KESTON<br>FIELDWORKS</span>
      </div>
    </div>

    <div class="person">
      <div class="name">DEAN HARLOW</div>
      <div class="role">Director</div>
    </div>

    <div class="social" aria-label="Social media">
      <span class="dot"></span>
      <span class="dot"></span>
      <span class="dot"></span>
    </div>

    <div class="contact">
      <div class="line">
        <span>0487305526</span>
        <svg viewBox="0 0 16 16" aria-hidden="true">
          <circle cx="8" cy="8" r="8" fill="rgba(255,255,255,0.85)"/>
          <path d="M4 6.5c0-1.5 8-1.5 8 0v1h-2v-1H6v1H4z M5.5 8h5l1 3.5h-7z" fill="#2ea6d8"/>
        </svg>
      </div>
      <div class="line">
        <span>dean@kolvat.biz</span>
        <svg viewBox="0 0 16 16" aria-hidden="true">
          <circle cx="8" cy="8" r="8" fill="rgba(255,255,255,0.85)"/>
          <rect x="4" y="5" width="8" height="6" fill="#2ea6d8"/>
          <path d="M4 5l4 3.2L12 5" fill="none" stroke="#fff" stroke-width="0.9"/>
        </svg>
      </div>
    </div>
  </section>

  <section class="card card-back">
    <div class="brand-circle"></div>
    <div class="brand-name">KESTON FIELDWORKS</div>
    <div class="website">www.kestonfieldworks.com</div>
  </section>

</div>
</body>
</html>
```